Redesign of Grown Builder of BRIXO Weblog.

I'm an Grown Builder of BRIXO (GBOB), and I'm the person behind a small, off-the-beaten-path fan site, built using PageLoom.

The existing site is at http://quarvelnook.example. As you can see, it could use an infinitely better design!

My site was originally for reviews of BRIXO sets, and had extended to include general commentary and a small gallery of models I've built and a cast of characters. It's particularly known for my opinions and perspective on the world of BRIXO, and as such isn't necessarily child friendly.
While keeping existing content, the new version of the site will focus more on video content from my ClipHarbor channel.

In contrast to the current site, I'm looking for a light design that makes use of a few muted, low saturation colours, whilst remaining clean and relatively simple. The logo is part of the site's identity and should serve as inspiration for the design.
The content pages would keep the thin floating menu, and the content area would be no more than 1200 pixels wide.
Though it's a BRIXO fan site, I would like to avoid overt references to BRIXO elements. Other that that, you're more than welcome to use your creative license with the design.

In addition to the home, blog and post pages, I would also like a "placeholder" page that can be adapted for different page types. I will be building the theme from the designs, so don't worry about doing any coding.
You don't have to provide them all at once at this stage: I would suggest submitting either the home page or post page.

The final design should communicate "this is MY corner of the web", but above all else that it's about creativity and self-expression.

If you have any questions, please get in touch!
Updates

Target Market(s)

People interested in BRIXO in general, 12 and up.

Industry/Entity Type

Adult

Number of Pages Required

4 page

Font styles to use
Sans Serif
Decorative
Other font styles liked:
• Qhytsdakx

Requirements
Must have
• The tagline "Make It Yours".
• I'm keeping the font/fount used for headings (Qhytsdakx); I'm open to suggestions for the body text.
Should not have
• Overt references to BRIXO or BRIXO elements.

```html
<!DOCTYPE html>
<html lang="en">
<head>
<meta charset="utf-8">
<title>Hushlane.tv — Make It Yours</title>
<link rel="stylesheet" href="https://fonts.googleapis.com/css2?family=Teko:wght@400;500&family=Open+Sans:wght@400;600;700&display=swap">
<style>
  :root {
    --ink: #333333;
    --body: #555555;
    --muted: #8a8a8a;
    --rule: #cfcfcf;
    --sky: #1aa6e8;
    --sky-dark: #222222;
    --hero-a: #3c3d40;
    --hero-b: #6a6b6e;
    --card-border: #dcdcdc;
    --card-top: #f2f2f2;
    --card-bottom: #ffffff;
    --arrow: #9a9a9a;
    --c-commentary: #1da8e0;
    --c-reviews: #e8901c;
    --c-mocs: #d9237f;
    --c-cast: #1f7a3a;
    --c-features: #2a1fa8;
    --c-photos: #d01b1b;
    --footer: #3a3a3a;
    --footer-bottom: #2b2b2b;
    --footer-text: #e6e6e6;
    --footer-rule: #555555;
    --link: #2ea8e6;
  }
  * { box-sizing: border-box; margin: 0; padding: 0; }
  html, body { width: 1200px; height: 2225px; overflow: hidden; background: #fff; }
  body { position: relative; font-family: "Open Sans", sans-serif; color: var(--body); }
  .display { font-family: "Teko", sans-serif; font-weight: 400; text-transform: uppercase; letter-spacing: 1px; }

  /* header */
  .site-header { position: absolute; top: 0; left: 0; width: 1200px; height: 119px; background: #fff; }
  .brand { position: absolute; left: 76px; top: 18px; height: 88px; display: flex; align-items: center; gap: 12px; }
  .brand-square { width: 70px; height: 88px; background: #222; }
  .brand-name { font-family: "Open Sans", sans-serif; font-weight: 700; font-size: 24px; color: #555; }
  .main-nav { position: absolute; left: 516px; top: 0; height: 107px; display: flex; }
  .main-nav a { display: block; height: 107px; line-height: 124px; font-size: 14px; font-weight: 600; color: var(--ink); text-decoration: none; }
  .main-nav .current { width: 89px; text-align: center; background: var(--sky); color: #fff; border-bottom: 11px solid var(--sky-dark); line-height: 124px; }
  .main-nav .n-commentary { margin-left: 25px; }
  .main-nav .n-reviews { margin-left: 42px; }
  .main-nav .n-mocs { margin-left: 47px; }
  .main-nav .n-features { margin-left: 41px; }
  .main-nav .n-cast { margin-left: 43px; }

  /* hero */
  .hero { position: absolute; top: 119px; left: 0; width: 1200px; height: 452px; background: linear-gradient(135deg, var(--hero-b), var(--hero-a) 60%, #2f3033); }
  .hero-title { position: absolute; left: 74px; top: 110px; font-size: 58px; line-height: 1; color: var(--sky); }
  .hero-text { position: absolute; left: 74px; top: 180px; width: 500px; font-family: "Teko", sans-serif; font-size: 29px; line-height: 41px; color: #fff; }
  .hero-arrows { position: absolute; left: 74px; top: 335px; }
  .hero-video { position: absolute; left: 614px; top: 59px; width: 510px; height: 334px; border: 6px solid #fff; background: linear-gradient(160deg, #8a8f96, #4a4c52 55%, #b9b9bc); }
  .play { position: absolute; left: 222px; top: 129px; }

  /* intro */
  .welcome-title { position: absolute; top: 612px; left: 0; width: 1200px; text-align: center; font-size: 40px; color: var(--ink); }
  .welcome-text { position: absolute; top: 668px; left: 82px; width: 1038px; text-align: center; font-size: 14px; line-height: 24px; color: var(--body); }
  .rule { position: absolute; left: 74px; width: 1050px; height: 1px; background: var(--rule); }

  /* sections */
  .section-head { position: absolute; width: 512px; text-align: center; }
  .section-head h2 { font-size: 36px; line-height: 40px; }
  .section-head p { margin: 6px auto 0; width: 430px; font-size: 14px; line-height: 23px; color: var(--body); }
  .card { position: absolute; width: 512px; height: 237px; border: 1px solid var(--card-border); background: linear-gradient(var(--card-top), var(--card-bottom)); }
  .thumb { position: absolute; top: 23px; width: 203px; height: 138px; border-radius: 3px; }
  .thumb.one { left: 38px; }
  .thumb.two { left: 268px; }
  .caption { position: absolute; top: 173px; width: 203px; text-align: center; font-size: 16px; font-weight: 600; line-height: 24px; color: #444; }
  .caption.one { left: 38px; }
  .caption.two { left: 268px; }
  .arrow { position: absolute; top: 108px; }
  .arrow.prev { left: 6px; }
  .arrow.next { left: 480px; }
  .photo { position: absolute; width: 131px; height: 86px; }

  /* footer */
  .site-footer { position: absolute; top: 1972px; left: 0; width: 1200px; height: 181px; background: var(--footer); }
  .footer-brand { position: absolute; left: 77px; top: 60px; height: 86px; display: flex; align-items: center; gap: 10px; }
  .footer-brand .brand-square { width: 66px; height: 86px; background: #1e1e1e; }
  .footer-brand .brand-name { font-size: 22px; color: #9a9a9a; }
  .footer-divider { position: absolute; top: 28px; width: 1px; height: 122px; background: var(--footer-rule); }
  .footer-heading { position: absolute; top: 26px; font-size: 24px; color: var(--sky); }
  .tweets { position: absolute; left: 326px; top: 66px; width: 360px; font-size: 13px; line-height: 23px; color: var(--footer-text); list-style: none; }
  .tweets li { margin-bottom: 4px; }
  .tweets span { display: block; color: var(--link); }
  .social { position: absolute; left: 732px; top: 64px; }
  .badge { position: absolute; left: 985px; width: 139px; height: 28px; }
  .badge.one { top: 33px; background: #7cc7ea; }
  .badge.two { top: 79px; background: #ffffff; }
  .footer-bottom { position: absolute; top: 2153px; left: 0; width: 1200px; height: 72px; background: var(--footer-bottom); text-align: center; padding-top: 20px; font-size: 11px; line-height: 15px; color: #b5b5b5; }
</style>
</head>
<body>

<header class="site-header">
  <div class="brand"><span class="brand-square"></span><span class="brand-name">hushlane.tv</span></div>
  <nav class="main-nav">
    <a class="current" href="#">HOME</a>
    <a class="n-commentary" href="#">COMMENTARY</a>
    <a class="n-reviews" href="#">REVIEWS</a>
    <a class="n-mocs" href="#">MOCS</a>
    <a class="n-features" href="#">FEATURES</a>
    <a class="n-cast" href="#">CAST</a>
  </nav>
</header>

<section class="hero" role="img" aria-label="Blurred background of many small toy figures">
  <h1 class="hero-title display">Make It Yours.</h1>
  <p class="hero-text">The home of Hushlane: a Grown Builder of BRIXO based in London, UK. Join us for commentary, banter, MOCs and our trademark antics.</p>
  <svg class="hero-arrows" width="86" height="50" viewBox="0 0 86 50" aria-hidden="true">
    <polyline points="30,4 10,25 30,46" fill="none" stroke="#fff" stroke-width="9"/>
    <polyline points="56,4 76,25 56,46" fill="none" stroke="#fff" stroke-width="9"/>
  </svg>
  <div class="hero-video" role="img" aria-label="Video still of a model shop window scene">
    <svg class="play" width="64" height="64" viewBox="0 0 64 64" aria-hidden="true">
      <circle cx="32" cy="32" r="32" fill="#fff"/>
      <polygon points="25,17 48,32 25,47" fill="#111"/>
    </svg>
  </div>
</section>

<h2 class="welcome-title display">Welcome to our website</h2>
<p class="welcome-text">Aliquam molestie, mi et imperdiet euismod, dui purus auctor tellus, et interdum lacus lectus et ante. Sed accumsan sollicitudin sapien, sit amet adipiscing turpis gravida ac. In congue, neque ac lobortis volutpat, libero mauris varius mi, vitae suscipit ipsum ligula vitae risus. Duis aliquam nibh a dui iaculis viverra id a velit. Vivamus egestas risus in magna varius commodo. Sed semper viverra egestas. Etiam pretium porttitor lectus, vel ornare neque porta volutpat.</p>

<div class="rule" style="top:771px"></div>

<!-- commentary -->
<div class="section-head" style="left:74px;top:800px"><h2 class="display" style="color:var(--c-commentary)">Commentary</h2><p>We give you our thoughts, opinions, rants and coverage on the world of BRIXO.</p></div>
<div class="card" style="left:74px;top:905px">
  <div class="thumb one" role="img" aria-label="Shop window display with yellow frame" style="background:linear-gradient(135deg,#6b5a12,#c9a51e 60%,#3b3620)"></div>
  <div class="thumb two" role="img" aria-label="Group of small figures in suits" style="background:linear-gradient(135deg,#bdbdbd,#4d4d4f 55%,#2a2a2c)"></div>
  <p class="caption one">Marlowe Windows at BLOKFEST 2015</p>
  <p class="caption two">Marlowe Windows at BLOKFEST 2015</p>
  <svg class="arrow prev" width="26" height="26" viewBox="0 0 26 26" aria-hidden="true"><circle cx="13" cy="13" r="12" fill="var(--arrow)"/><polyline points="15,7 9,13 15,19" fill="none" stroke="#fff" stroke-width="3"/></svg>
  <svg class="arrow next" width="26" height="26" viewBox="0 0 26 26" aria-hidden="true"><circle cx="13" cy="13" r="12" fill="var(--arrow)"/><polyline points="11,7 17,13 11,19" fill="none" stroke="#fff" stroke-width="3"/></svg>
</div>

<!-- reviews -->
<div class="section-head" style="left:612px;top:800px"><h2 class="display" style="color:var(--c-reviews)">Reviews</h2><p>We no longer do reviews, but the ones we've done are here for your perusal.</p></div>
<div class="card" style="left:612px;top:905px">
  <div class="thumb one" role="img" aria-label="Colourful boxed set" style="background:linear-gradient(135deg,#8a5fa8,#d9a4c4 55%,#6d4a8a)"></div>
  <div class="thumb two" role="img" aria-label="Grey lab-style model set" style="background:linear-gradient(135deg,#5a5a5c,#c8c8c8 55%,#3a3a3c)"></div>
  <p class="caption one">Marlowe Windows at BLOKFEST 2015</p>
  <p class="caption two">Marlowe Windows at BLOKFEST 2015</p>
  <svg class="arrow prev" width="26" height="26" viewBox="0 0 26 26" aria-hidden="true"><circle cx="13" cy="13" r="12" fill="var(--arrow)"/><polyline points="15,7 9,13 15,19" fill="none" stroke="#fff" stroke-width="3"/></svg>
  <svg class="arrow next" width="26" height="26" viewBox="0 0 26 26" aria-hidden="true"><circle cx="13" cy="13" r="12" fill="var(--arrow)"/><polyline points="11,7 17,13 11,19" fill="none" stroke="#fff" stroke-width="3"/></svg>
</div>

<div class="rule" style="top:1182px"></div>

<!-- mocs -->
<div class="section-head" style="left:74px;top:1208px"><h2 class="display" style="color:var(--c-mocs)">MOCs</h2><p>Short for My Own Creations: BRIXO models built by Hushlane.</p></div>
<div class="card" style="left:74px;top:1312px">
  <div class="thumb one" role="img" aria-label="Living room model with yellow sofas" style="background:linear-gradient(135deg,#5d5a2a,#b8b04a 55%,#6b5d3a)"></div>
  <div class="thumb two" role="img" aria-label="Pool scene model from above" style="background:linear-gradient(135deg,#3d4f8a,#c7d3e0 55%,#4a5470)"></div>
  <p class="caption one">Marlowe Windows at BLOKFEST 2015</p>
  <p class="caption two">Marlowe Windows at BLOKFEST 2015</p>
  <svg class="arrow prev" width="26" height="26" viewBox="0 0 26 26" aria-hidden="true"><circle cx="13" cy="13" r="12" fill="var(--arrow)"/><polyline points="15,7 9,13 15,19" fill="none" stroke="#fff" stroke-width="3"/></svg>
  <svg class="arrow next" width="26" height="26" viewBox="0 0 26 26" aria-hidden="true"><circle cx="13" cy="13" r="12" fill="var(--arrow)"/><polyline points="11,7 17,13 11,19" fill="none" stroke="#fff" stroke-width="3"/></svg>
</div>

<!-- cast -->
<div class="section-head" style="left:612px;top:1208px"><h2 class="display" style="color:var(--c-cast)">Cast</h2><p>Meet the many faces of Hushlane.tv!</p></div>
<div class="card" style="left:612px;top:1312px">
  <div class="thumb one" role="img" aria-label="Cast member figure on orange backdrop" style="background:linear-gradient(135deg,#b4431c,#d8d2c8 55%,#b4431c)"></div>
  <div class="thumb two" role="img" aria-label="Two cast member figures on orange backdrop" style="background:linear-gradient(135deg,#c24a1e,#2e7a3a 45%,#a8261e)"></div>
  <p class="caption one">Marlowe Windows at BLOKFEST 2015</p>
  <p class="caption two">Marlowe Windows at BLOKFEST 2015</p>
  <svg class="arrow prev" width="26" height="26" viewBox="0 0 26 26" aria-hidden="true"><circle cx="13" cy="13" r="12" fill="var(--arrow)"/><polyline points="15,7 9,13 15,19" fill="none" stroke="#fff" stroke-width="3"/></svg>
  <svg class="arrow next" width="26" height="26" viewBox="0 0 26 26" aria-hidden="true"><circle cx="13" cy="13" r="12" fill="var(--arrow)"/><polyline points="11,7 17,13 11,19" fill="none" stroke="#fff" stroke-width="3"/></svg>
</div>

<div class="rule" style="top:1594px"></div>

<!-- features -->
<div class="section-head" style="left:74px;top:1631px"><h2 class="display" style="color:var(--c-features)">Features</h2></div>
<div class="card" style="left:74px;top:1692px">
  <div class="thumb one" role="img" aria-label="Red carpet event scene with figures" style="background:linear-gradient(160deg,#d8d8d8,#b02020 60%,#5a1414)"></div>
  <div class="thumb two" role="img" aria-label="Small vehicle models on grey" style="background:linear-gradient(135deg,#8a8894,#3a3a40 55%,#9a94b8)"></div>
  <p class="caption one">Marlowe Windows at BLOKFEST 2015</p>
  <p class="caption two">Marlowe Windows at BLOKFEST 2015</p>
  <svg class="arrow prev" width="26" height="26" viewBox="0 0 26 26" aria-hidden="true"><circle cx="13" cy="13" r="12" fill="var(--arrow)"/><polyline points="15,7 9,13 15,19" fill="none" stroke="#fff" stroke-width="3"/></svg>
  <svg class="arrow next" width="26" height="26" viewBox="0 0 26 26" aria-hidden="true"><circle cx="13" cy="13" r="12" fill="var(--arrow)"/><polyline points="11,7 17,13 11,19" fill="none" stroke="#fff" stroke-width="3"/></svg>
</div>

<!-- photostream -->
<div class="section-head" style="left:612px;top:1631px"><h2 class="display" style="color:var(--c-photos)">Snapvale Photostream</h2></div>
<div class="card" style="left:612px;top:1692px">
  <div class="photo" role="img" aria-label="Figure photo" style="left:45px;top:25px;background:linear-gradient(135deg,#6a6a6a,#c9a636)"></div>
  <div class="photo" role="img" aria-label="Figure photo" style="left:190px;top:25px;background:linear-gradient(135deg,#5a5a5a,#3f6a3a)"></div>
  <div class="photo" role="img" aria-label="Figure photo" style="left:336px;top:25px;background:linear-gradient(135deg,#7a4a2a,#c48a3a)"></div>
  <div class="photo" role="img" aria-label="Figure photo" style="left:45px;top:128px;background:linear-gradient(135deg,#6a6a6a,#a8281e)"></div>
  <div class="photo" role="img" aria-label="Figure photo" style="left:190px;top:128px;background:linear-gradient(135deg,#6e6e6e,#c9b070)"></div>
  <div class="photo" role="img" aria-label="Figure photo" style="left:336px;top:128px;background:linear-gradient(135deg,#6a6a6a,#c98a3a)"></div>
  <svg class="arrow prev" width="26" height="26" viewBox="0 0 26 26" aria-hidden="true"><circle cx="13" cy="13" r="12" fill="var(--arrow)"/><polyline points="15,7 9,13 15,19" fill="none" stroke="#fff" stroke-width="3"/></svg>
  <svg class="arrow next" width="26" height="26" viewBox="0 0 26 26" aria-hidden="true"><circle cx="13" cy="13" r="12" fill="var(--arrow)"/><polyline points="11,7 17,13 11,19" fill="none" stroke="#fff" stroke-width="3"/></svg>
</div>

<footer class="site-footer">
  <div class="footer-brand"><span class="brand-square"></span><span class="brand-name">hushlane.tv</span></div>
  <div class="footer-divider" style="left:279px"></div>
  <h3 class="footer-heading display" style="left:326px">Chirpline Feeds</h3>
  <ul class="tweets">
    <li>Marlowe Windows at BLOKFEST 2015<span>https://lnk.example/9KnDnjuawG https://lnk.example/vNHLFw8cft #.</span></li>
    <li>Marlowe Windows at BLOKFEST 2015<span>https://lnk.example/9KnDnjuawG https://lnk.example/vNHLFw8cft #.</span></li>
  </ul>
  <div class="footer-divider" style="left:696px"></div>
  <h3 class="footer-heading display" style="left:728px">Follow us</h3>
  <svg class="social" width="220" height="40" viewBox="0 0 220 40" role="img" aria-label="Social network links">
    <g stroke="#fff" stroke-width="3">
      <circle cx="18" cy="20" r="17" fill="#3b5998"/>
      <circle cx="63" cy="20" r="17" fill="#1da1f2"/>
      <circle cx="107" cy="20" r="17" fill="#c8c8c8"/>
      <circle cx="152" cy="20" r="17" fill="#d34836"/>
      <circle cx="196" cy="20" r="17" fill="#cc2020"/>
    </g>
  </svg>
  <div class="badge one" role="img" aria-label="Partner badge"></div>
  <div class="badge two" role="img" aria-label="Partner badge"></div>
</footer>
<div class="footer-bottom">
  <p>Copyright ©2016 Hushlane.tv, all rights reserved.</p>
  <p>BRIXO® is a registered trademark of The BRIXO Group, who has no connection with Hushlane.tv whatsoever</p>
</div>

</body>
</html>
```